Website for IT consulting Company

I need a website upgrade, the existing site content is ok, I would also like to add a testimonial page, the site should be something that is easy for us to update content. You use the content from www.kelvanbrook.com as an example. I will also post update logo and artwork. I also need a contact form with some type of validation or captcha.

I added Coded to the Project

Please omit Address maps

Target Market(s)

small business, service oriented companies. We provide IT Consulting, support and mangement

Industry/Entity Type

Information Technology

Coding

Number of Pages Required

1 page

Font styles to use
Serif
Sans Serif

Requirements
Must have
• Contain logo attached, and content from existing web site www.kelvanbrook.com.
• Also need to update content easily, and be movable to different platforms.
• There is a catch phrase
• "Let us worry about your technology…” “ so you don’t have to!”
• Should be included.
Nice to have
• Testimonial page, Project page where we can post new and past projects and pictures
Should not have
• none

```html
<!DOCTYPE html>
<html lang="en">
<head>
<meta charset="utf-8">
<title>Kelvanbrook Development Group</title>
<link rel="stylesheet" href="https://fonts.googleapis.com/css2?family=Exo+2:ital,wght@0,700;0,800;1,700;1,800&family=Arimo:wght@400;700&family=PT+Serif&display=swap">
<style>
:root{
  --blue:#1d8fd6;
  --blue-dark:#1473b5;
  --blue-light:#39a9ea;
  --ink:#1e1e1e;
  --text:#333;
  --grey-bg:#e6e6e6;
  --grey-mid:#9a9a9a;
  --grey-dark:#6e6e6e;
  --top:#2b2b2b;
  --footer:#262a30;
  --white:#fff;
}
*{box-sizing:border-box;margin:0;padding:0}
html,body{width:1200px;height:2927px;overflow:hidden}
body{font-family:"Arimo",Arial,sans-serif;color:var(--text);background:var(--white);position:relative}
.display{font-family:"Exo 2",sans-serif;font-style:italic;font-weight:800}
section,header,nav,footer,div{position:absolute}

.topbar{left:0;top:0;width:1200px;height:39px;background:var(--top)}
.topbar .social{position:absolute;top:6px;width:26px;height:26px;background:#8d8d8d;border-radius:3px}

.masthead{left:0;top:39px;width:1200px;height:86px;background:var(--white);border-top:3px solid var(--blue-light)}
.brand{left:78px;top:22px;display:flex;align-items:center;gap:12px}
.brand .mark{width:38px;height:38px;background:var(--blue)}
.brand .name{font-family:"Exo 2",sans-serif;font-weight:800;font-size:34px;color:#555;letter-spacing:1px}
.phone{left:908px;top:26px;display:flex;align-items:center;gap:14px;font-family:"Exo 2",sans-serif;font-style:italic;font-weight:700;font-size:21px;color:#444}
.phone .ico{width:28px;height:28px;background:var(--blue);border-radius:3px;display:flex;align-items:center;justify-content:center}

.mainnav{left:0;top:125px;width:1200px;height:56px;background:linear-gradient(#3aa9ea,#1b86cc)}
.mainnav a{position:absolute;top:17px;font-family:"Exo 2",sans-serif;font-style:italic;font-weight:800;font-size:18px;color:var(--white);text-decoration:none;letter-spacing:.5px}
.mainnav a.current{color:#1b3550}

.hero{left:0;top:181px;width:1200px;height:535px;background:radial-gradient(ellipse at 48% 40%,#5b7c99 0%,#25364a 35%,#11161d 75%)}
.hero .caption{left:0;bottom:0;width:1200px;height:58px;background:rgba(20,20,20,.75);text-align:center;line-height:58px;font-size:32px;color:var(--white)}
.hero .caption span{color:var(--blue-light)}

.welcome{left:0;top:716px;width:1200px;height:425px}
.welcome h1{position:absolute;left:84px;top:58px;width:650px;white-space:nowrap;font-size:20px;color:var(--ink);letter-spacing:0}
.welcome h1 span{color:var(--blue)}
.welcome .rule{left:84px;top:90px;width:96px;height:3px;background:var(--blue)}
.welcome .copy{left:84px;top:118px;width:636px;font-size:13.5px;line-height:24px;color:#222}
.welcome .copy p{margin-bottom:10px}
.inquiry{left:765px;top:37px;width:354px;height:332px;background:#ececec;border:1px solid #d6d6d6}
.inquiry .tab{left:48px;top:-10px;width:258px;height:44px;background:linear-gradient(#8f8f8f,#6f6f6f);color:var(--white);font-size:20px;text-align:center;line-height:44px}
.inquiry .field{position:absolute;left:20px;width:314px;height:36px;background:var(--white);border:1px solid #d4d4d4;font-size:12px;color:#777;padding:10px 12px}
.inquiry .submit{left:26px;top:266px;width:124px;height:36px;background:linear-gradient(#3aa9ea,#1a84c9);color:var(--white);font-size:19px;text-align:center;line-height:36px}

.services{left:0;top:1141px;width:1200px;height:572px;background:var(--grey-bg);overflow:hidden}
.services h2{position:absolute;left:0;width:1200px;top:42px;text-align:center;font-size:29px;color:var(--ink)}
.services h2 span{color:var(--blue)}
.services .rule{left:566px;top:86px;width:68px;height:3px;background:var(--blue)}
.services svg{position:absolute;left:0;top:0}
.svc-label{font-family:"Exo 2",sans-serif;font-style:italic;font-weight:800;font-size:16px;fill:#222}

.panels{left:0;top:1713px;width:1200px;height:388px}
.panel{top:0;height:388px}
.panel.support{left:0;width:605px;background:linear-gradient(#2da0e2,#1577ba)}
.panel.outsource{left:605px;width:595px;background:linear-gradient(#c9c9c9,#8c8c8c)}
.panel h3{position:absolute;top:66px;font-size:24px;color:var(--white)}
.panel.outsource h3{color:var(--ink)}
.panel .hr{top:108px;height:2px;width:120px;background:rgba(255,255,255,.6)}
.panel .photo{top:131px;width:205px;height:185px}
.panel .blurb{top:130px;font-size:13.5px;line-height:24px;color:var(--white)}
.panel .more{top:278px;width:152px;height:40px;font-family:"PT Serif",serif;font-size:17px;color:var(--white);line-height:40px;padding-left:18px}

.testimonials{left:0;top:2101px;width:1200px;height:354px;background:var(--white)}
.testimonials h2{position:absolute;left:0;width:1200px;top:50px;text-align:center;font-size:29px;color:var(--ink)}
.testimonials h2 span{color:var(--blue)}
.testimonials .rule{left:566px;top:92px;width:68px;height:3px;background:var(--blue)}
.testimonials blockquote{position:absolute;left:210px;top:142px;width:780px;text-align:center;font-style:italic;font-size:14.5px;line-height:33px;color:#222}
.testimonials .who{left:0;width:1200px;top:262px;text-align:center;font-size:16px;font-weight:700;color:#222;line-height:22px}
.testimonials svg{position:absolute}

.cta{left:0;top:2455px;width:1200px;height:101px;background:linear-gradient(#3aa9ea,#1a82c6)}
.cta p{position:absolute;left:86px;font-size:32px;color:var(--white)}
.cta .callbtn{left:853px;top:25px;width:210px;height:49px;background:linear-gradient(#9a9a9a,#6b6b6b);border-radius:10px;color:var(--white);font-size:17px;line-height:20px;padding:5px 0 0 38px}

.site-footer{left:0;top:2556px;width:1200px;height:328px;background:linear-gradient(#3b4049,#1d2026)}
.site-footer h4{position:absolute;top:64px;font-size:18px;color:var(--white)}
.site-footer h4 span{color:var(--blue-light)}
.site-footer ul{position:absolute;list-style:none;font-size:13px;color:#e8e8e8}
.quick li{line-height:25px;padding-left:16px;position:relative}
.quick li::before{content:"";position:absolute;left:0;top:11px;width:4px;height:4px;background:var(--blue-light)}
.contact-lines{left:320px;top:102px;font-size:13px;line-height:21px;color:#e8e8e8}
.social-list li{height:45px;display:flex;align-items:center;gap:16px}
.social-list .sq{width:28px;height:28px;background:#bdbdbd;border-radius:2px}
.footer-mark{left:896px;top:50px;width:150px;height:150px;background:var(--blue);opacity:.85}

.copyright{left:0;top:2884px;width:1200px;height:43px;background:var(--blue);text-align:center;line-height:43px;font-size:14px;font-weight:700;color:var(--white)}
</style>
</head>
<body>

<header class="topbar">
  <span class="social" style="left:976px"></span>
  <span class="social" style="left:1011px"></span>
  <span class="social" style="left:1046px"></span>
  <span class="social" style="left:1081px"></span>
</header>

<div class="masthead">
  <div class="brand"><span class="mark"></span><span class="name">KELVANBROOK</span></div>
  <div class="phone">
    <span class="ico"><svg width="16" height="16" viewBox="0 0 24 24"><path d="M6.6 10.8a15.1 15.1 0 0 0 6.6 6.6l2.2-2.2a1 1 0 0 1 1-.25 11.4 11.4 0 0 0 3.6.57 1 1 0 0 1 1 1V20a1 1 0 0 1-1 1A17 17 0 0 1 3 4a1 1 0 0 1 1-1h3.5a1 1 0 0 1 1 1c0 1.25.2 2.45.57 3.57a1 1 0 0 1-.25 1z" fill="#fff"/></svg></span>
    (555) 014-2290
  </div>
</div>

<nav class="mainnav">
  <a class="current" href="#" style="left:98px">HOME</a>
  <a href="#" style="left:224px">ABOUT US</a>
  <a href="#" style="left:385px">SERVICES</a>
  <a href="#" style="left:546px">SUPPORT</a>
  <a href="#" style="left:695px">CLIENTS</a>
  <a href="#" style="left:841px">CAREERS</a>
  <a href="#" style="left:991px">CONTACT&nbsp; US</a>
</nav>

<section class="hero" role="img" aria-label="Hand touching a glowing laptop icon surrounded by floating device icons">
  <div class="caption display">Let Us Worry About Your Technology... <span>So You Don't Have To!</span></div>
</section>

<section class="welcome">
  <h1 class="display">WELCOME TO <span>KELVANBROOK DEVELOPMENT GROUP, INC</span></h1>
  <div class="rule"></div>
  <div class="copy">
    <p>Kelvanbrook Development Group, Inc. was established in 1991. Our mission is helping businesses and individuals realize a Return on Investment by implementing today's advanced technologies. As a small business we understand the importance of technology and personalized attention. Every member of our support team has worked with both large and small companies supporting a multitude of applications, networks and environments.</p>
    <p>We interface daily with Clients and their customers to establish your support needs. A prerequisite for working with Kelvanbrook is having both the technological knowledge and the customer skills to communicate and work with customers to resolve technology issues. Whether it is a simple computer network, phone systems, or an advanced integrated infrastructure, we will study your requirements, suggest methodologies, and implement the design.</p>
  </div>
  <div class="inquiry">
    <div class="tab display">Quick Inquiry</div>
    <span class="field" style="top:52px">First Name</span>
    <span class="field" style="top:94px">Email</span>
    <span class="field" style="top:136px">Phone</span>
    <span class="field" style="top:178px;height:78px">Message</span>
    <div class="submit display">Submit</div>
  </div>
</section>

<section class="services">
  <h2 class="display">OUR <span>SERVICES</span></h2>
  <div class="rule"></div>
  <svg width="1200" height="572" viewBox="0 0 1200 572">
    <circle cx="615" cy="572" r="262" fill="none" stroke="#9c9c9c" stroke-width="9"/>
    <circle cx="615" cy="572" r="256" fill="#fff"/>
    <g stroke="#9c9c9c" stroke-width="2" stroke-dasharray="3 3">
      <line x1="365" y1="500" x2="264" y2="471" stroke="#d33" />
      <line x1="401" y1="425" x2="314" y2="365"/>
      <line x1="458" y1="364" x2="395" y2="280"/>
      <line x1="533" y1="326" x2="499" y2="226"/>
      <line x1="615" y1="312" x2="615" y2="207"/>
      <line x1="697" y1="326" x2="731" y2="226"/>
      <line x1="772" y1="364" x2="835" y2="280"/>
      <line x1="829" y1="425" x2="916" y2="365"/>
      <line x1="865" y1="500" x2="966" y2="471"/>
    </g>
    <g fill="#fff" stroke="#9c9c9c" stroke-width="3">
      <circle cx="365" cy="500" r="8" stroke="#d33"/>
      <circle cx="401" cy="425" r="8"/><circle cx="458" cy="364" r="8"/>
      <circle cx="533" cy="326" r="8"/><circle cx="615" cy="312" r="8"/>
      <circle cx="697" cy="326" r="8"/><circle cx="772" cy="364" r="8"/>
      <circle cx="829" cy="425" r="8"/><circle cx="865" cy="500" r="8"/>
    </g>
    <g stroke="#fff" stroke-width="4">
      <circle cx="264" cy="471" r="44" fill="var(--blue)"/>
      <circle cx="314" cy="365" r="44" fill="#8a8a8a"/>
      <circle cx="395" cy="280" r="44" fill="#8a8a8a"/>
      <circle cx="499" cy="226" r="44" fill="#8a8a8a"/>
      <circle cx="615" cy="207" r="44" fill="#8a8a8a"/>
      <circle cx="731" cy="226" r="44" fill="#8a8a8a"/>
      <circle cx="835" cy="280" r="44" fill="#8a8a8a"/>
      <circle cx="916" cy="365" r="44" fill="#8a8a8a"/>
      <circle cx="966" cy="471" r="44" fill="#8a8a8a"/>
    </g>
    <g fill="none" stroke="#fff" stroke-width="3">
      <rect x="248" y="458" width="32" height="20" rx="2"/><line x1="242" y1="484" x2="286" y2="484"/>
      <circle cx="306" cy="356" r="8"/><rect x="318" y="362" width="16" height="12"/><path d="M294 380a12 10 0 0 1 24 0"/>
      <line x1="395" y1="268" x2="395" y2="300"/><path d="M383 300l12-24 12 24"/><path d="M385 262a14 14 0 0 0 0 16M405 262a14 14 0 0 1 0 16"/>
      <circle cx="499" cy="226" r="18"/><line x1="494" y1="218" x2="494" y2="234"/><line x1="504" y1="218" x2="504" y2="234"/>
      <rect x="599" y="190" width="32" height="10" rx="2"/><rect x="599" y="203" width="32" height="10" rx="2"/><circle cx="627" cy="222" r="8"/>
      <rect x="713" y="215" width="26" height="18" rx="2"/><rect x="742" y="214" width="10" height="20" rx="2"/>
      <path d="M822 295l20-28 10 7-20 28z"/><path d="M842 267l6-6"/>
      <rect x="898" y="368" width="36" height="10" rx="3"/><path d="M906 360a14 14 0 0 1 20 0M900 352a22 22 0 0 1 32 0"/>
      <path d="M966 452l16 6v12c0 10-8 16-16 20-8-4-16-10-16-20v-12z"/>
    </g>
    <text class="svc-label" x="206" y="487" text-anchor="end">DESKTOP</text>
    <text class="svc-label" x="206" y="505" text-anchor="end">SUPPORT</text>
    <text class="svc-label" x="250" y="357" text-anchor="end">NETWORK</text>
    <text class="svc-label" x="250" y="374" text-anchor="end">ADMINISTRATION</text>
    <text class="svc-label" x="330" y="272" text-anchor="end">TELECOMMUNICATIONS</text>
    <text class="svc-label" x="448" y="199" text-anchor="end">AUDIO/VIDEO MULTIMEDIA</text>
    <text class="svc-label" x="620" y="139" text-anchor="middle">DISASTER RECOVERY</text>
    <text class="svc-label" x="784" y="188">WEB DESIGN</text>
    <text class="svc-label" x="900" y="272">NETWORK CABLING</text>
    <text class="svc-label" x="982" y="363">WIRELESS</text>
    <text class="svc-label" x="982" y="380">NETWORKS</text>
    <text class="svc-label" x="1016" y="477">ANTIVIRUS</text>
    <text class="svc-label" x="1016" y="494">SOLUTIONS</text>
    <rect x="486" y="478" width="22" height="22" fill="var(--blue)"/>
    <text x="518" y="500" font-family="Exo 2, sans-serif" font-weight="800" font-size="34" fill="#666">KELVANBROOK</text>
  </svg>
</section>

<section class="panels">
  <div class="panel support">
    <svg style="position:absolute;left:84px;top:62px" width="26" height="30" viewBox="0 0 26 30"><circle cx="13" cy="8" r="7" fill="#fff"/><path d="M1 30c0-9 5-14 12-14s12 5 12 14z" fill="#fff"/></svg>
    <h3 class="display" style="left:128px">IT SUPPORT SOLUTIONS</h3>
    <div class="hr" style="left:84px"></div>
    <div class="photo" style="left:84px;background:linear-gradient(135deg,#4a6f8c,#c9d6df 55%,#2b3e50)" role="img" aria-label="Technicians working in a server room"></div>
    <div class="blurb" style="left:310px;width:285px">Lorem ipsum dolor sit amet, consectetur adipiscing elit, sed diam nonummy nibh euismod tincidunt ut laoreet et dolore magna aliquam erat volutpat. Ut wisi enim consequat.</div>
    <div class="more" style="left:310px;background:linear-gradient(#a9a9a9,#7c7c7c)">Read More &rarr;</div>
  </div>
  <div class="panel outsource">
    <svg style="position:absolute;left:30px;top:64px" width="30" height="30" viewBox="0 0 30 30"><circle cx="15" cy="7" r="5" fill="#222"/><circle cx="5" cy="12" r="4" fill="#222"/><circle cx="25" cy="12" r="4" fill="#222"/><path d="M7 30c0-8 3-14 8-14s8 6 8 14z" fill="#222"/></svg>
    <h3 class="display" style="left:72px">WHY OUTSOURCE TECHNOLOGIES</h3>
    <div class="hr" style="left:30px;background:rgba(255,255,255,.7)"></div>
    <div class="photo" style="left:33px;background:radial-gradient(circle at 50% 40%,#7fb4e6,#1d3c66 60%,#0b1526)" role="img" aria-label="Hand holding a tablet with a glowing globe above it"></div>
    <div class="blurb" style="left:253px;width:305px">Lorem ipsum dolor sit amet, consectetur adipiscing elit, sed diam nonummy nibh euismod tincidunt ut laoreet et dolore magna aliquam erat volutpat. Ut wisi enim consequat.</div>
    <div class="more" style="left:253px;background:linear-gradient(#3aa9ea,#1a82c6)">Read More &rarr;</div>
  </div>
  <svg style="position:absolute;left:575px;top:0" width="60" height="30" viewBox="0 0 60 30"><path d="M0 0h60L30 30z" fill="#fff"/></svg>
</section>

<section class="testimonials">
  <h2 class="display">CLIENTS <span>TESTIMONIALS</span></h2>
  <div class="rule"></div>
  <blockquote><span style="font-size:30px;color:#aaa">&ldquo;</span> Lorem ipsum dolor sit amet, consectetuer adipiscing elit, sed diam nonummy nibh euismod tincidunt ut laoreet dolore magna aliquam erat volutpat. Ut wisi enim ad minim veniam, quis nostrud exercitorn morkle tation ullamcorper suscipit lobortis nisl ut aliquip ex ea commodo consequat. <span style="font-size:30px;color:#aaa">&rdquo;</span></blockquote>
  <div class="who">Marla T.<br><span style="font-size:15px">Lindenport, CA</span></div>
  <svg style="left:116px;top:194px" width="30" height="56" viewBox="0 0 30 56"><path d="M28 2L3 28l25 26" fill="none" stroke="#bbb" stroke-width="2"/></svg>
  <svg style="left:1054px;top:194px" width="30" height="56" viewBox="0 0 30 56"><path d="M2 2l25 26L2 54" fill="none" stroke="#bbb" stroke-width="2"/></svg>
</section>

<section class="cta">
  <p class="display" style="top:14px">IT Solutions That Work For Your Business</p>
  <p class="display" style="top:54px">A Full Service Technology Company</p>
  <div class="callbtn display">Call Us Today<br>(555) 014-2290</div>
</section>

<footer class="site-footer" role="img" aria-label="Dim city skyline at dusk behind the footer">
  <h4 class="display" style="left:86px">Quick <span>Links</span></h4>
  <ul class="quick" style="left:86px;top:96px">
    <li>Home</li><li>About Us</li><li>Services</li><li>Support</li><li>Clients</li><li>Careers</li><li>Contact Us</li>
  </ul>
  <h4 class="display" style="left:320px">Contact <span>Details</span></h4>
  <div class="contact-lines">
    Kelvanbrook Development Group, Inc.<br>
    <div style="position:static;margin-top:12px">418 Marlow Ave.<br>Fairhaven, Texas 77990</div>
    <div style="position:static;margin-top:16px;line-height:34px">&#9742;&nbsp; (555) 014-2290<br>&#9113;&nbsp; (555) 014-2291<br>&#9993;&nbsp; info@kelvanbrook.com</div>
  </div>
  <h4 class="display" style="left:654px">Get <span>Social</span></h4>
  <ul class="social-list" style="left:654px;top:91px">
    <li><span class="sq"></span>Pagebook</li>
    <li><span class="sq"></span>Chirper</li>
    <li><span class="sq"></span>Circleplus</li>
    <li><span class="sq"></span>Worknet</li>
  </ul>
  <div class="footer-mark"></div>
</footer>

<div class="copyright">Copyright &copy; 2017 Kelvanbrook Development Group, Inc. All Rights Reserved.</div>

</body>
</html>
```